4th Generation Family Business Needs a New Card Design!

We are a family owned 4th Generation company. We are based in the Sydney, Australia area and we are desperately in need of a more modern and classy card. We are monumental masons who design, supply & erect lasting memorials throughout cemeteries in Sydney. Our customers are normally in a period of grieving. I have attached logo files that will need to be implemented on the card. Company was established 1935. Australian Owned and Operated. Card needs to be designed to PIXO.com specification.

Target Market(s)

Our target market is based upon people that a grieving for family members that have passed away. We also deal with alot of companies that own and operate cemeteries.

Industry/Entity Type

Business

Contact Information for Business Card

Simon Harcourt, Operations Manager, 0417293086, simon@harcourtmemorials.com.au
Lewis Harcourt, Director, 0491630572, lewis@harcourtmemorials.com.au
Phone # 02 9561 3048
Website: www.harcourtmemorials.com.au
Address: Suite 17, 8 Palfrey Lane, West Carlow, Sydney NSW 2156

Font styles to use
Serif
Decorative
Script

Requirements
Must have
• Would like to see the logo nicely implemented with a modern design. Embossed lettering would be a nice additive.

```html
<!DOCTYPE html>
<html lang="en">
<head>
<meta charset="utf-8">
<title>Harcourt Memorials – Business Card</title>
<link rel="stylesheet" href="https://fonts.googleapis.com/css2?family=Open+Sans:ital,wght@0,400;0,700;1,400;1,700&display=swap">
<style>
  :root {
    --backdrop: #5b5b5d;
    --card: #fdfbf9;
    --ink: #1e1e1e;
    --ink-soft: #2c2c2c;
    --gilt: #c9951f;
  }
  * { margin: 0; padding: 0; box-sizing: border-box; }
  html, body {
    width: 1200px; height: 675px; overflow: hidden;
    background: var(--backdrop);
    font-family: "Open Sans", Arial, sans-serif;
    color: var(--ink);
  }
  .canvas {
    position: relative; width: 1200px; height: 675px;
  }
  .card {
    position: absolute; top: 185px;
    width: 500px; height: 305px;
    background: var(--card);
    border-bottom: 4px solid var(--gilt);
  }
  .card--front { left: 60px; }
  .card--back { left: 640px; }

  .contact {
    position: absolute; left: 40px; top: 112px;
  }
  .contact__name {
    font-weight: 700; font-size: 15.5px; letter-spacing: 0.6px;
    text-transform: uppercase;
  }
  .contact__role {
    font-style: italic; font-size: 12px; margin-top: 1px; margin-left: -2px;
  }
  .contact__lines {
    list-style: none; margin-top: 10px; font-style: italic; font-size: 11.5px;
    line-height: 17px; color: var(--ink-soft);
  }
  .contact__lines b { font-weight: 700; }
  .contact__web {
    font-weight: 700; font-style: italic; font-size: 12px; margin-top: 1px;
  }

  .address {
    position: absolute; right: 44px; top: 170px;
    text-align: right; font-size: 11.5px; line-height: 16px;
    font-style: normal; color: var(--ink-soft);
  }

  .brand {
    position: absolute; inset: 0;
    display: flex; align-items: center; justify-content: center; gap: 12px;
  }
  .brand__mark {
    width: 16px; height: 16px; background: var(--ink);
  }
  .brand__name {
    font-size: 26px; font-weight: 400; letter-spacing: 1.5px;
    text-transform: uppercase; color: var(--ink); text-align: center; line-height: 1.15;
  }
</style>
</head>
<body>
<main class="canvas">
  <section class="card card--front" aria-label="Card front">
    <div class="contact">
      <h1 class="contact__name">Simon Harcourt</h1>
      <p class="contact__role">Operations Manager</p>
      <ul class="contact__lines">
        <li><b>C</b> : 0417293086</li>
        <li><b>P</b> : 02 9561 3048</li>
        <li><b>E</b> : simon@harcourtmemorials.com.au</li>
      </ul>
      <p class="contact__web">www.harcourtmemorials.com.au</p>
    </div>
    <address class="address">
      Suite 17<br>
      8 Palfrey Lane<br>
      West Carlow<br>
      Sydney NSW 2156
    </address>
  </section>

  <section class="card card--back" aria-label="Card back">
    <div class="brand">
      <span class="brand__mark"></span>
      <p class="brand__name">Harcourt<br>Memorials</p>
    </div>
  </section>
</main>
</body>
</html>
```